We are a local Communty Pharmacy wishing to promote and market a specialised Pharmaceutical Service

We would like a design that is professional and enticing ( according to the brief In attached files)
We wish to Market Compounding Pharmacy as a specialist side of our business.
We have the expertise a purpose built preparation laboratory.
The main purpose is an Internet presence that entices prospective patients to contact or visit our physical store.

Target Market(s)

Patients Medicos and Veterinary clients

Industry/Entity Type

Pharmacy

Coding

Coded - Design and coding required

Number of Pages Required

1 page

Requirements
Must have
• Clear friendly image
Nice to have
• soft enticing feel
Should not have
• No crass loud unprofessional elements

```html
<!DOCTYPE html>
<html lang="en">
<head>
<meta charset="utf-8">
<title>Brookvale Compounding</title>
<link href="https://fonts.googleapis.com/css2?family=Roboto:wght@400;500;700&family=Roboto+Condensed:wght@400;700&display=swap" rel="stylesheet">
<style>
:root{
  --green:#7dc243;
  --green-dark:#5fa32b;
  --slate:#56646b;
  --lilac:#9a8fc6;
  --ink:#3b3f42;
  --muted:#8a8f93;
  --line:#e3e5e6;
  --footer:#24292c;
  --page:#ffffff;
}
*{margin:0;padding:0;box-sizing:border-box}
html,body{width:739px;height:1200px;overflow:hidden;background:var(--page)}
body{font-family:"Roboto",Arial,sans-serif;color:var(--ink);font-size:8px;line-height:1.5;position:relative}
.wrap{position:absolute;left:62px;width:615px}
h1,h2,h3,h4{font-family:"Roboto Condensed","Arial Narrow",sans-serif;font-weight:700}

/* header */
.header{top:0;height:92px}
.brand{position:absolute;left:0;top:26px;display:flex;align-items:center;gap:8px}
.brand-mark{width:30px;height:30px;background:var(--green);border-radius:50%}
.brand-name{font-family:"Roboto Condensed",sans-serif;font-weight:700;font-size:18px;color:var(--green-dark);line-height:1}
.topright{position:absolute;right:0;top:8px;width:260px;text-align:right}
.toolbar{display:flex;gap:3px;justify-content:flex-end;align-items:center;white-space:nowrap;height:15px}
.social-box{display:block;width:15px;height:15px;background:var(--green);flex:none}
.acct{margin-left:10px;font-size:7px;line-height:15px;color:var(--muted);display:flex;align-items:center;gap:3px}
.acct::before{content:"";width:6px;height:6px;background:var(--green);border-radius:1px}
.call-note{margin-top:10px;font-size:7px;line-height:10px;color:var(--muted);white-space:nowrap}
.phone{margin-top:2px;display:flex;gap:5px;justify-content:flex-end;align-items:center;font-size:14px;line-height:18px;font-weight:700;color:var(--green-dark);white-space:nowrap}

/* nav */
.nav{top:92px;height:28px;background:#f1f2f2;border:1px solid var(--line);display:flex;align-items:center}
.nav a{font-family:"Roboto Condensed",sans-serif;font-weight:700;font-size:8px;color:var(--ink);text-decoration:none;padding:0 16px;height:100%;display:flex;align-items:center}
.nav a.active{background:var(--green);color:#fff}
.search{margin-left:auto;margin-right:10px;width:130px;height:17px;background:#fff;border:1px solid var(--line);display:flex;align-items:center;justify-content:space-between;padding:0 5px;color:var(--muted);font-size:7px}

/* hero */
.hero-band{position:absolute;left:0;top:200px;width:739px;height:170px;background:var(--green)}
.hero{top:148px;height:280px;display:flex}
.hero-copy{width:270px;flex:none;background:var(--green);padding:40px 20px 0;color:#fff;position:relative}
.hero-copy h1{font-size:16px;line-height:1.2;font-weight:400}
.hero-copy h1 strong{display:block;margin-top:2px;font-size:21px;font-weight:700;white-space:nowrap}
.hero-copy p{margin-top:12px;font-size:7px;opacity:.9}
.btn{display:inline-block;margin-top:14px;padding:5px 10px;font-family:"Roboto Condensed",sans-serif;font-weight:700;font-size:7px;text-transform:uppercase;text-decoration:none}
.btn-ghost{border:1px solid #fff;color:#fff}
.btn-green{background:var(--green);color:#fff}
.btn-line{border:1px solid var(--line);color:var(--ink)}
.dots{position:absolute;left:20px;bottom:14px;display:flex;gap:5px}
.dots i{width:7px;height:7px;border-radius:50%;border:1px solid #fff}
.dots i.on{background:#fff}
.hero-photo{flex:1;background:linear-gradient(120deg,#e9eef0,#c9d5d9 60%,#f3f5f4)}

/* about */
.about{top:455px;height:150px}
.about-text{position:absolute;left:0;top:20px;width:395px}
.about-text h2{font-size:16px;color:var(--ink)}
.about-text p{margin-top:8px;font-size:7px;color:var(--muted)}
.about-photos{position:absolute;right:0;top:10px;display:flex;gap:4px}
.about-photos div{width:100px;height:122px;background:linear-gradient(140deg,#dfe7ea,#b9c8cd)}

/* services */
.services{top:635px;height:178px;display:flex;gap:12px}
.card{flex:1;color:#fff;text-align:center;padding:18px 14px 0}
.card.green{background:var(--green)}
.card.slate{background:var(--slate)}
.card.lilac{background:var(--lilac)}
.card .icon{width:34px;height:34px;border:2px solid #fff;border-radius:50%;margin:0 auto;display:flex;align-items:center;justify-content:center}
.card h3{margin-top:12px;font-size:10px}
.card p{margin-top:6px;font-size:7px;opacity:.92}

/* news */
.news{top:825px;height:120px;display:flex;gap:25px}
.post{flex:1}
.post h4{font-size:10px;padding-bottom:5px;border-bottom:1px solid var(--line)}
.meta{margin-top:6px;font-size:6.5px;color:var(--green-dark)}
.post p{margin-top:5px;font-size:7px;color:var(--muted)}
.post-foot{display:flex;justify-content:space-between;align-items:flex-end}
.pager{display:flex;gap:3px}
.pager span{width:12px;height:10px;background:#d9dcdd}

/* footer */
.footer{position:absolute;left:0;top:967px;width:739px;height:233px;background:var(--footer);color:#c9cdcf}
.footer h4{font-size:11px;color:#fff}
.footer h4 em{font-style:normal;color:var(--green)}
.f-contact{position:absolute;left:62px;top:22px;width:170px;font-size:7px}
.f-contact p{margin-top:6px}
.f-hours{position:absolute;left:292px;top:22px;width:200px;font-size:7px}
.f-hours li{list-style:none;margin-top:5px;display:flex;gap:5px;align-items:center}
.f-hours li::before{content:"";width:6px;height:6px;background:var(--green);border-radius:50%}
.f-hours b{color:#fff}
.f-map{position:absolute;left:510px;top:22px;width:167px;height:118px;background:linear-gradient(135deg,#d9dcd7,#bfc5be)}
.f-social{position:absolute;left:0;top:163px;width:739px;display:flex;gap:5px;justify-content:center}
.f-social span{width:20px;height:20px;border:1px solid #4a5256;border-radius:50%}
.f-copy{position:absolute;left:0;top:196px;width:739px;text-align:center;font-size:6.5px;color:#7d8488}
</style>
</head>
<body>

<header class="wrap header">
  <div class="brand"><span class="brand-mark"></span><span class="brand-name">BROOKVALE<br>COMPOUNDING</span></div>
  <div class="topright">
    <div class="toolbar">
      <span class="social-box"></span><span class="social-box"></span><span class="social-box"></span><span class="social-box"></span>
      <span class="acct">Login</span><span class="acct">Cart (0) item</span>
    </div>
    <div class="call-note">(Pharmacy) For Urgent Needs Call Us at</div>
    <div class="phone">
      <svg width="12" height="12" viewBox="0 0 24 24"><path fill="#5fa32b" d="M6.6 10.8a15 15 0 0 0 6.6 6.6l2.2-2.2c.3-.3.7-.4 1-.2 1.1.4 2.3.6 3.6.6.6 0 1 .4 1 1V20c0 .6-.4 1-1 1A17 17 0 0 1 3 4c0-.6.4-1 1-1h3.5c.6 0 1 .4 1 1 0 1.3.2 2.5.6 3.6.1.3 0 .7-.2 1z"/></svg>
      (555) 0134 678 210
    </div>
  </div>
</header>

<nav class="wrap nav">
  <a class="active" href="#">HOME</a><a href="#">ABOUT US</a><a href="#">PRODUCTS</a><a href="#">EVENT</a><a href="#">CONTACT US</a>
  <div class="search">Search
    <svg width="8" height="8" viewBox="0 0 24 24"><circle cx="10" cy="10" r="6" fill="none" stroke="#8a8f93" stroke-width="3"/><path d="M15 15l6 6" stroke="#8a8f93" stroke-width="3"/></svg>
  </div>
</nav>

<div class="hero-band"></div>
<section class="wrap hero">
  <div class="hero-copy">
    <h1>WHAT WE ARE IN THE SPECIALTY BUSINESS OF<strong>COMPOUNDING PHARMACY</strong></h1>
    <p>Personalised medicines prepared in our own laboratory, made to suit each patient, prescriber and animal in our care.</p>
    <a class="btn btn-ghost" href="#">Read more</a>
    <div class="dots"><i class="on"></i><i></i><i></i><i></i></div>
  </div>
  <div class="hero-photo" role="img" aria-label="Smiling pharmacist in a white coat standing in a pharmacy"></div>
</section>

<section class="wrap about">
  <div class="about-text">
    <h2>WHAT IS COMPOUNDING PHARMACY?</h2>
    <p>Compounding is the craft of preparing a medicine to match the exact needs of one patient. When a standard product is not the right strength, form or flavour, our trained pharmacists create a tailored version in our purpose built laboratory. We work closely with doctors, specialists and vets so every preparation is safe, precise and easy to take. From creams and capsules to liquids without dyes or allergens, we help people and pets receive the treatment they truly need. Visit our store or call our team to learn how a personalised medicine could make daily care simpler for you and your family.</p>
    <a class="btn btn-green" href="#">Read more</a>
  </div>
  <div class="about-photos">
    <div role="img" aria-label="Pharmacy shelves stocked with medicines"></div>
    <div role="img" aria-label="Pharmacist holding a medicine box"></div>
  </div>
</section>

<section class="wrap services">
  <article class="card green">
    <div class="icon"><svg width="16" height="16" viewBox="0 0 24 24"><path fill="#fff" d="M10 3h4v7h7v4h-7v7h-4v-7H3v-4h7z"/></svg></div>
    <h3>COMMUNITY PHARMACY</h3>
    <p>Friendly local advice, prescriptions and everyday health products for the whole family, close to home.</p>
  </article>
  <article class="card slate">
    <div class="icon"><svg width="16" height="16" viewBox="0 0 24 24"><circle cx="12" cy="8" r="4" fill="#fff"/><path fill="#fff" d="M4 21c0-4.4 3.6-7 8-7s8 2.6 8 7z"/></svg></div>
    <h3>DISPENSING DOCTORS</h3>
    <p>We support prescribers with custom strengths and forms, prepared quickly and checked with care.</p>
  </article>
  <article class="card lilac">
    <div class="icon"><svg width="16" height="16" viewBox="0 0 24 24"><rect x="4" y="4" width="16" height="16" fill="none" stroke="#fff" stroke-width="2"/><path fill="#fff" d="M11 7h2v4h4v2h-4v4h-2v-4H7v-2h4z"/></svg></div>
    <h3>HOSPITAL PHARMACY</h3>
    <p>Reliable compounded preparations for clinics and wards, made to strict quality standards.</p>
  </article>
</section>

<section class="wrap news">
  <article class="post">
    <h4>MAECENAS ALIQUAM NEC ODIO</h4>
    <div class="meta">● 24 MAY 2015 &nbsp; ● Author: Pharmacist &nbsp; ● Tags: 12</div>
    <p>Learn how tailored doses can help patients who struggle with standard tablets, and why more families now ask their local pharmacist about compounding options.</p>
    <div class="post-foot"><a class="btn btn-line" href="#">Read more</a></div>
  </article>
  <article class="post">
    <h4>MAECENAS ALIQUAM NEC ODIO</h4>
    <div class="meta">● 24 MAY 2015 &nbsp; ● Author: Pharmacist &nbsp; ● Tags: 12</div>
    <p>Our laboratory team shares tips on flavoured liquids for children and pets, making daily medicine time calmer and easier for everyone at home.</p>
    <div class="post-foot"><a class="btn btn-line" href="#">Read more</a><div class="pager"><span></span><span></span></div></div>
  </article>
</section>

<footer class="footer">
  <div class="f-contact">
    <h4>CONTACT <em>INFO</em></h4>
    <p>1420 Elmwood Crescent,<br>Brookvale, CA 90210</p>
    <p>Tel: (555) 0134 678 210 &nbsp; Fax: (555) 0134 678 211</p>
    <p>E: hello@brookvalecompounding.com</p>
    <p>Call us or drop in any day and our friendly team will be happy to help.</p>
  </div>
  <div class="f-hours">
    <h4>OPENING <em>HOURS</em></h4>
    <ul>
      <li><b>Monday</b> 08 am to 06 pm</li>
      <li><b>Tuesday</b> 08 am to 06 pm</li>
      <li><b>Wednesday</b> 08 am to 06 pm</li>
      <li><b>Thursday</b> 08 am to 06 pm</li>
      <li><b>Friday</b> 08 am to 06 pm</li>
      <li><b>Saturday</b> 09 am to 01 pm</li>
    </ul>
  </div>
  <div class="f-map" role="img" aria-label="Street map showing the pharmacy location"></div>
  <div class="f-social"><span></span><span></span><span></span><span></span><span></span></div>
  <div class="f-copy">Copyright © 2015 Brookvale Compounding. All rights reserved.</div>
</footer>

</body>
</html>
```